"Thornbury Accupuncture" needs a Promotional Card - A6 size

Requirements
Must have
• Bright colours, pictures of happy people, acupuncture-related pictures.

```html
<!DOCTYPE html>
<html lang="en">
<head>
<meta charset="utf-8">
<title>Thornbury Acupuncture – Promotional Cards</title>
<link rel="stylesheet" href="https://fonts.googleapis.com/css2?family=Open+Sans:ital,wght@0,400;0,600;0,700;1,400&display=swap">
<style>
  :root {
    --page-bg: #e4e2df;
    --card-bg: #ffffff;
    --brand-red: #e4542b;
    --brand-orange: #f39325;
    --brand-yellow: #f6d336;
    --text-grey: #555555;
    --text-dark: #333333;
    --skin: #e9c8b6;
    --photo-frame: #f3d07a;
  }
  * { box-sizing: border-box; margin: 0; padding: 0; }
  html, body { width: 1200px; height: 926px; overflow: hidden; }
  body { background: var(--page-bg); font-family: "Open Sans", Arial, sans-serif; color: var(--text-grey); position: relative; }

  .card { position: absolute; width: 495px; height: 700px; background: var(--card-bg); overflow: hidden; box-shadow: 0 6px 18px rgba(0,0,0,.18); }
  .card--front { left: 90px; top: 100px; }
  .card--back { left: 625px; top: 135px; }
  .card__footer-bar { position: absolute; left: 0; right: 0; bottom: 0; height: 12px; background: var(--brand-red); }

  .photo { position: absolute; }
  .brand-name { position: absolute; font-weight: 700; color: var(--brand-red); line-height: 1.05; text-align: center; }
  .brand-name__dot { display: block; width: 22px; height: 22px; border-radius: 50%; background: var(--brand-yellow); margin: 0 auto 6px; }
  .wave { position: absolute; left: 0; width: 100%; }

  /* Front */
  .front__photo { left: 0; top: 0; width: 495px; height: 300px; background: linear-gradient(160deg, #f4ddd0 0%, var(--skin) 45%, #f7ece6 100%); }
  .front__brand { right: 18px; top: 36px; font-size: 20px; }
  .front__wave { top: 170px; height: 160px; }
  .front__headline { position: absolute; left: 20px; right: 20px; top: 325px; text-align: center; font-size: 18px; color: var(--brand-red); line-height: 1.35; }
  .front__about { position: absolute; left: 26px; right: 24px; top: 397px; font-size: 10px; font-style: italic; line-height: 1.42; }
  .front__about h2 { font-size: 10px; font-weight: 600; color: var(--text-dark); }
  .front__offer { position: absolute; left: 26px; right: 20px; top: 540px; font-size: 12px; font-weight: 700; color: var(--brand-red); line-height: 1.4; }
  .front__more { position: absolute; left: 0; right: 0; top: 584px; text-align: center; font-size: 13px; color: var(--text-dark); line-height: 1.4; }
  .front__more b { font-weight: 600; }
  .front__call { position: absolute; left: 26px; top: 634px; font-size: 16px; color: var(--text-dark); line-height: 1.3; }
  .front__phone { color: var(--brand-red); font-weight: 700; }
  .front__phone svg { vertical-align: -2px; }
  .social { position: absolute; right: 22px; top: 642px; display: flex; gap: 6px; }
  .social__square { width: 31px; height: 31px; border-radius: 3px; }
  .social__square--a { background: #3b5998; }
  .social__square--b { background: #55acee; }
  .social__square--c { background: #ee7a6c; }

  /* Back */
  .back__photo { left: 0; top: 0; width: 495px; height: 265px; background: linear-gradient(180deg, #b9c99a 0%, #e8d3c0 55%, #f0dfd3 100%); }
  .back__wave { top: 190px; height: 110px; }
  .back__brand { right: 20px; top: 215px; font-size: 25px; }
  .back__intro { position: absolute; left: 25px; right: 22px; top: 326px; font-size: 10.5px; line-height: 1.4; }
  .back__headline { position: absolute; left: 25px; top: 404px; font-size: 13.5px; font-weight: 700; color: var(--brand-red); line-height: 1.3; }
  .back__question { position: absolute; left: 25px; top: 444px; font-size: 11px; font-style: italic; color: var(--text-dark); }
  .conditions { position: absolute; left: 25px; top: 476px; display: grid; grid-template-columns: 120px 120px; row-gap: 2px; list-style: none; font-size: 11px; color: var(--text-dark); }
  .conditions li::before { content: ""; display: inline-block; width: 7px; height: 7px; border-radius: 50%; background: var(--brand-red); margin-right: 5px; }
  .gallery__title { position: absolute; left: 296px; top: 396px; font-size: 15px; color: var(--brand-red); }
  .gallery__photo { position: absolute; left: 296px; width: 176px; height: 83px; border: 1px solid var(--photo-frame); }
  .gallery__photo--back { top: 417px; background: linear-gradient(180deg, #f6e3d8, #e8bca6 60%, #f8eee8); }
  .gallery__photo--hands { top: 505px; background: linear-gradient(160deg, #f3e2d6, #deb199 55%, #f4e7df); }
  .gallery__photo--beach { top: 596px; background: linear-gradient(180deg, #b9dcef 0%, #f4e4c3 55%, #e3c99d 100%); }
  .practitioner__photo { position: absolute; left: 15px; top: 583px; width: 90px; height: 105px; background: linear-gradient(180deg, #ecece8, #cfb7a8 60%, #9b7d88); }
  .practitioner__name { position: absolute; left: 102px; top: 625px; font-size: 14px; color: var(--brand-red); }
  .practitioner__quals { position: absolute; left: 104px; top: 646px; font-size: 10.5px; color: var(--text-dark); line-height: 1.25; }
  .member-badge { position: absolute; left: 240px; top: 617px; width: 44px; text-align: center; }
  .member-badge__circle { width: 40px; height: 40px; border-radius: 50%; background: #1fa5b5; margin: 0 auto 4px; }
  .member-badge__label { font-size: 7px; color: #1fa5b5; line-height: 1.1; }
</style>
</head>
<body>

<article class="card card--front">
  <div class="photo front__photo" role="img" aria-label="Close-up of a practitioner's hand placing acupuncture needles in a patient's shoulder"></div>
  <svg class="wave front__wave" viewBox="0 0 495 160" preserveAspectRatio="none" aria-hidden="true">
    <path d="M0 95 C120 20 260 150 495 40 L495 95 C300 170 150 60 0 130 Z" fill="#f6d336"/>
    <path d="M0 115 C140 40 280 150 495 70 L495 110 C300 180 140 80 0 160 Z" fill="#f39325"/>
    <path d="M0 140 C150 90 280 170 495 95 L495 160 L0 160 Z" fill="#ffffff"/>
    <path d="M0 100 C150 40 300 140 495 55" fill="none" stroke="#f6d336" stroke-width="1.5"/>
    <path d="M0 125 C160 70 300 150 495 80" fill="none" stroke="#f39325" stroke-width="1"/>
  </svg>
  <div class="brand-name front__brand"><span class="brand-name__dot"></span>Thornbury<br>Acupuncture</div>

  <h1 class="front__headline">Acupuncture improves the well-being and<br>contribute to physical and emotional balance.</h1>

  <section class="front__about">
    <h2>About Acupuncture and Mirela</h2>
    <p>Mirela Dancheva has a passion for helping people to stay healthy without the need for drugs. She graduated with a BSc (hons) from the respected Meridian College of Eastern Medicine in Reading.</p>
    <p>Mirela also has a BSc in physiotherapy and 9 years' experience working in the public health service.</p>
    <p>Acupuncture is a holistic therapy practised for more than 2500 years in China and now popular around the world.</p>
    <p>Mirela stimulates specific points on the body to assist the body's own healing ability, balancing its energy and boosting the feeling of well-being.</p>
  </section>

  <p class="front__offer">Contact Mirela for a free, 15-minute, no-obligation consultation and find out how acupuncture can help you.</p>

  <p class="front__more">To find out more about acupuncture, visit<br>Mirela's website <b>www.thornburyclinic.com</b> | <b>@thornburyacupuncture</b></p>

  <p class="front__call">Call <span class="front__phone"><svg width="15" height="15" viewBox="0 0 16 16" aria-hidden="true"><circle cx="8" cy="8" r="7" fill="none" stroke="#e4542b" stroke-width="1.5"/><path d="M5.5 4.5 L7 4.5 L7.5 6.5 L6.6 7.2 C7 8.2 7.8 9 8.8 9.4 L9.5 8.5 L11.5 9 L11.5 10.5 C8 11 5 8 5.5 4.5 Z" fill="#e4542b"/></svg> +44 7700 900123</span><br>to book your appointment</p>

  <div class="social" aria-hidden="true">
    <span class="social__square social__square--a"></span>
    <span class="social__square social__square--b"></span>
    <span class="social__square social__square--c"></span>
  </div>
  <div class="card__footer-bar"></div>
</article>

<article class="card card--back">
  <div class="photo back__photo" role="img" aria-label="Three generations of a happy family laughing together on a sofa"></div>
  <svg class="wave back__wave" viewBox="0 0 495 110" preserveAspectRatio="none" aria-hidden="true">
    <path d="M0 55 C140 10 300 90 495 10 L495 110 L0 110 Z" fill="#f6d336"/>
    <path d="M0 85 C150 35 300 95 495 30 L495 110 L0 110 Z" fill="#ffffff"/>
  </svg>
  <div class="brand-name back__brand"><span class="brand-name__dot"></span>Thornbury<br>Acupuncture</div>

  <p class="back__intro">Mirela Dancheva is a qualified acupuncturist with a special interest in helping patients with these and many other health issues. To learn about the current research in acupuncture for the different conditions visit the National Needle Therapy Register website, www.needleregister.org.uk</p>

  <h2 class="back__headline">Chinese medicine and acupuncture<br>can improve your well-being.</h2>
  <p class="back__question">Do you suffer from any of the following?</p>
  <ul class="conditions">
    <li>Anxiety</li><li>Stress</li>
    <li>Problems walking</li><li>PMS</li>
    <li>Chronic pain</li><li>Arthritis</li>
    <li>Depression</li><li>Headache</li>
    <li>Insomnia</li><li>Menopausal symptoms?</li>
  </ul>

  <h3 class="gallery__title">IMPROVED WELL-BEING</h3>
  <div class="gallery__photo gallery__photo--back" role="img" aria-label="Hands resting on a lower back showing pain relief"></div>
  <div class="gallery__photo gallery__photo--hands" role="img" aria-label="Practitioner holding a patient's hand during treatment"></div>
  <div class="gallery__photo gallery__photo--beach" role="img" aria-label="Couple walking hand in hand along a sunny beach"></div>

  <div class="practitioner__photo" role="img" aria-label="Portrait of the acupuncturist"></div>
  <p class="practitioner__name">Mirela Dancheva</p>
  <p class="practitioner__quals">BSc(hons) physiotherapy<br>BSc(hons) acupuncture</p>

  <div class="member-badge">
    <div class="member-badge__circle" aria-hidden="true"></div>
    <p class="member-badge__label">Register Member</p>
  </div>
  <div class="card__footer-bar"></div>
</article>

</body>
</html>
```